Soy Candle Labels

We sell soy candles in recycled wine bottles. The wine bottle is cut in half and filled with pure and natural soy wax and scented with essential oils.
Our product represents good use of up cycling materials for a better use. The product is all natural and eco friendly.
You can see good use of labels and branding for a company in America that does the same thing http://larkmeadow7wicks.example/
Trya dn keep the label uncomplicated like the above labels.
We will need an area to hand stamp the scent. Similar to the labels used on the above website.
We would prefer to use a white or off white paper label with gold or bronze printing - limit the use of colour and keep the label simple and sophisticated.
Emberlace Candle Co. is our company name. Emberlace being the predominant name and candle co. written small underneath right justified.
Die cut labels might look better than a rectangle.
Dimensions should be 90mm Wide x 90mm High
The final design should communicate a professional and quality product. But stay modern and professional. Clean, elegant and sophisticated.
Can use wording such as: Hand Poured, Premium Soy Wax, All Natural, Up cycled
Have a look at the attached image for the look and feel we are going for.
Updates
Designers are having a little bit of trouble interpreting the brief into a viable design. To assist perhaps you can look at WINE LABELS on google images. Design your label around an existing style wine label to give the canld ethe feel of being a bottle of wine. Get creative! :)
Reason: We require more designs. We havnt quite got what were looking for.
Please see brief.

```html
<!DOCTYPE html>
<html lang="en">
<head>
<meta charset="utf-8">
<title>Emberlace Candle Co. – Soy Candle Label</title>
<link rel="stylesheet" href="https://fonts.googleapis.com/css2?family=Cinzel:wght@400&family=Oswald:wght@500&display=swap">
<style>
  :root {
    --label-cream: #fefbe3;
    --bronze: #b8692a;
    --ring-tan: #dca882;
    --stamp-sage: #a9bf8c;
  }
  html, body {
    margin: 0;
    padding: 0;
    overflow: hidden;
    background: var(--label-cream);
  }
  .label {
    position: relative;
    width: 1200px;
    height: 1200px;
    background: var(--label-cream);
    overflow: hidden;
    font-family: "Cinzel", "Times New Roman", serif;
    color: var(--bronze);
  }
  .meta {
    position: absolute;
    top: 34px;
    margin: 0;
    font-size: 25px;
    letter-spacing: 0.5px;
    font-weight: 400;
  }
  .meta--origin { left: 68px; }
  .meta--weight { right: 68px; }

  .brand-name {
    position: absolute;
    right: 62px;
    top: 520px;
    margin: 0;
    font-size: 168px;
    font-weight: 400;
    line-height: 1;
    letter-spacing: 2px;
  }
  .brand-sub {
    position: absolute;
    right: 60px;
    top: 752px;
    margin: 0;
    font-size: 46px;
    font-weight: 400;
    letter-spacing: 1px;
  }

  .claims {
    position: absolute;
    left: 68px;
    top: 922px;
    margin: 0;
    font-size: 31px;
    letter-spacing: 0.5px;
  }
  .claims__divider { margin: 0 14px; }

  .rule-double {
    position: absolute;
    left: 0;
    top: 984px;
    width: 691px;
    height: 11px;
    border-top: 3px solid var(--bronze);
    border-bottom: 3px solid var(--bronze);
    box-sizing: border-box;
  }

  .scent-caption {
    position: absolute;
    left: 787px;
    top: 990px;
    margin: 0;
    font-size: 27px;
    transform: rotate(-90deg);
    transform-origin: center;
    letter-spacing: 1px;
  }
  .scent-stamp {
    position: absolute;
    left: 858px;
    top: 855px;
    width: 300px;
    height: 300px;
  }
  .scent-stamp__text {
    position: absolute;
    inset: 0;
    display: flex;
    flex-direction: column;
    align-items: center;
    justify-content: center;
    margin: 0;
    font-family: "Oswald", "Arial Narrow", sans-serif;
    font-weight: 500;
    font-size: 66px;
    line-height: 1.05;
    color: var(--stamp-sage);
    letter-spacing: 1px;
  }

  .base-band {
    position: absolute;
    left: 0;
    bottom: 0;
    width: 1200px;
    height: 15px;
    background: var(--bronze);
  }
</style>
</head>
<body>
  <main class="label">
    <p class="meta meta--origin">Product of Australia</p>
    <p class="meta meta--weight">320 gm. Premium Soy Wax</p>

    <h1 class="brand-name">Emberlace</h1>
    <p class="brand-sub">Candle Co.</p>

    <p class="claims">Hand Poured<span class="claims__divider">|</span>All Natural Soy</p>
    <div class="rule-double"></div>

    <p class="scent-caption">Scent</p>
    <div class="scent-stamp">
      <svg width="300" height="300" viewBox="0 0 300 300" aria-hidden="true">
        <circle cx="150" cy="150" r="146" fill="none" stroke="var(--ring-tan)" stroke-width="4"/>
      </svg>
      <p class="scent-stamp__text"><span>SCENT</span><span>NAME</span></p>
    </div>

    <div class="base-band"></div>
  </main>
</body>
</html>
```